Vigil Ledger Suite (Web Design)

Design with your logo. Background in black or dark. Elegant style, it's a website for professional people only. Our company provides a cloud software manager for Funeral Services Companies.

Target Market(s)

Professional of Funeral Services.

Coding

Coded - Design and coding required

Number of Pages Required

3 page

Font styles to use
Sans Serif

Colors
fbee3d
000000
5c5c5c

Requirements
Must have
• Design of the website should be similar to our logo colors.

```html
<!DOCTYPE html>
<html lang="en">
<head>
<meta charset="utf-8">
<title>Vigil Ledger Suite</title>
<link rel="stylesheet" href="https://fonts.googleapis.com/css2?family=Montserrat:wght@400;500;600;700;800&family=Open+Sans:wght@400;600&display=swap">
<style>
:root{
  --yellow:#fbee3d;
  --black:#000000;
  --grey:#5c5c5c;
  --header:#3b3b3b;
  --white:#ffffff;
  --soft:#d9d9d9;
  --head-font:"Montserrat",sans-serif;
  --body-font:"Open Sans",sans-serif;
}
*{box-sizing:border-box;margin:0;padding:0}
html,body{width:1200px;height:4401px;overflow:hidden;background:var(--black)}
body{position:relative;font-family:var(--body-font);color:var(--white)}
section,header,footer{position:absolute;left:0;width:1200px;overflow:hidden}
.abs{position:absolute}
svg{display:block}

/* header */
.site-header{top:0;height:135px;background:var(--header);z-index:3}
.brand{left:100px;top:30px;font-family:var(--head-font);font-weight:800;color:var(--yellow);font-size:30px;line-height:1;letter-spacing:1px;display:flex;align-items:center;gap:12px}
.brand-dot{width:22px;height:22px;border-radius:50%;background:var(--yellow)}
.contact-chip{left:522px;top:22px;display:flex;align-items:center;gap:10px;font-size:14px;line-height:1.15}
.chip-icon{width:30px;height:30px;border-radius:50%;background:var(--yellow);display:flex;align-items:center;justify-content:center}
.lang{left:710px;top:22px;display:flex;align-items:center;gap:10px;font-size:14px;line-height:1.15}
.flag{width:38px;height:38px;border-radius:50%;background:linear-gradient(180deg,#c4323b 0 50%,#f1f1f1 50% 100%);}
.search{left:860px;top:20px;width:246px;height:40px;border-radius:20px;background:var(--white);display:flex;align-items:center;padding:0 6px 0 14px;color:#888;font-size:14px;gap:8px}
.search span{flex:1}
.search-btn{width:30px;height:30px;border-radius:50%;background:var(--yellow);display:flex;align-items:center;justify-content:center}
.main-nav{top:88px;left:402px;display:flex;gap:0;font-family:var(--head-font);font-size:16px;font-weight:500}
.main-nav a{color:var(--white);text-decoration:none;position:absolute;white-space:nowrap}

/* hero */
.hero{top:135px;height:640px}
.hero-photo{left:0;top:0;width:1200px;height:640px;background:linear-gradient(100deg,#2b2c28 0%,#4a4b44 35%,#5f5c55 60%,#2a2624 100%)}
.hero-figure{left:730px;top:0;width:400px;height:610px;background:linear-gradient(180deg,#6d6150 0%,#2a2622 45%,#121212 100%);border-radius:160px 160px 0 0;opacity:.85}
.hero-brand{left:92px;top:115px;font-family:var(--head-font);font-weight:800;color:var(--yellow);font-size:62px;line-height:1.05;letter-spacing:1px}
.hero-copy{left:92px;top:318px;width:560px;font-size:16px;line-height:2}
.swoosh{position:absolute;left:0;width:1200px}

/* about */
.about{top:748px;height:580px}
.about-photo{left:103px;top:59px;width:440px;height:440px;border-radius:50%;border:8px solid var(--yellow);background:radial-gradient(circle at 50% 40%,#8a8f94,#3f4549 70%,#24292c)}
.about-body{left:584px;top:128px;width:514px}
.section-title{font-family:var(--head-font);font-weight:600;font-size:36px;letter-spacing:1px}
.about-body .section-title{color:var(--yellow);font-size:38px;font-weight:700}
.about-body p{margin-top:12px;font-size:14.5px;line-height:2;text-align:justify}
.btn{display:inline-flex;align-items:center;justify-content:center;background:var(--yellow);color:var(--black);font-family:var(--head-font);font-weight:600;font-size:16px}
.about-body .btn{margin-top:18px;width:138px;height:40px}

/* services */
.services{top:1320px;height:704px;background:radial-gradient(ellipse at 50% 55%,#0f2238 0%,#0b1420 45%,#050608 85%)}
.center{left:0;width:1200px;text-align:center}
.services .section-title{top:145px}
.lead{font-size:15px;line-height:2.1}
.services .lead{top:196px;left:240px;width:720px}
.service-card{top:288px;width:320px;height:255px;border:2px solid var(--yellow);text-align:center;padding-top:32px}
.service-card h3{font-family:var(--head-font);font-weight:600;font-size:18px;margin-top:14px;letter-spacing:.5px}
.service-card p{font-size:12.5px;line-height:1.85;margin:8px 34px 0}
.read-more{font-size:12.5px;font-weight:600;display:inline-flex;gap:8px;align-items:center;margin-top:4px}
.slide-arrow{top:400px}

/* blog */
.blog{top:2024px;height:560px;background:var(--black)}
.blog .section-title{top:58px}
.post{top:124px;width:328px}
.post-img{height:190px;background:linear-gradient(135deg,#2a4f7c,#0d1f3a 60%,#1b2a3d)}
.post-date{position:absolute;left:18px;top:178px;height:28px;padding:0 12px;background:var(--yellow);color:var(--black);font-size:13px;font-weight:600;display:flex;align-items:center;gap:7px}
.post h3{font-family:var(--head-font);font-weight:600;font-size:17px;margin-top:42px}
.post p{font-size:12.5px;line-height:1.9;margin-top:8px}
.post .more{font-family:var(--head-font);font-weight:700;font-size:12.5px;margin-top:12px}

/* testimonials */
.testimonials{top:2582px;height:680px;background:linear-gradient(180deg,#0a0a0a 0%,#1a1d22 40%,#101216 70%,#050505 100%)}
.testimonials .section-title{top:208px}
.quote-mark{left:570px;top:262px}
.testimonials blockquote{top:322px;left:180px;width:840px;text-align:center;font-size:19px;line-height:1.95}
.author{top:446px;font-family:var(--head-font);font-weight:600;font-size:17px}
.t-arrow{top:330px}

/* contact */
.contact{top:3257px;height:580px;background:var(--black)}
.contact .section-title{top:80px}
.contact .lead{top:128px;left:170px;width:860px}
.field{height:36px;border:1.5px solid #d0d0d0;display:flex;align-items:center;gap:8px;padding:0 14px;font-size:12.5px;color:var(--white)}
.field.message{align-items:flex-start;padding-top:8px}
.submit{left:519px;top:452px;width:153px;height:49px;gap:10px;font-size:18px}

/* footer */
.site-footer{top:3829px;height:572px;background:linear-gradient(180deg,#0a0b0d 0%,#141820 50%,#0b0c0f 100%)}
.footer-brand{top:128px;font-family:var(--head-font);font-weight:800;color:var(--yellow);font-size:44px;letter-spacing:1px}
.info{top:264px;width:320px;text-align:center;font-size:17px;line-height:1.7}
.info-icon{width:88px;height:88px;border-radius:50%;background:var(--yellow);display:flex;align-items:center;justify-content:center;margin:0 auto 14px}
.footer-links{top:438px;font-size:14.5px;font-weight:600}
.footer-links span.sep{margin:0 10px;color:var(--soft)}
.copyright{top:480px;font-size:13.5px;color:var(--soft)}
.social{top:520px;left:534px;display:flex;gap:12px}
.social span{width:30px;height:30px;border:1.5px solid var(--white);border-radius:50%}
</style>
</head>
<body>

<header class="site-header">
  <div class="abs brand"><span class="brand-dot"></span>Vigil Ledger Suite</div>
  <div class="abs contact-chip">
    <span class="chip-icon"><svg width="16" height="16" viewBox="0 0 24 24"><path d="M6.6 10.8a15 15 0 0 0 6.6 6.6l2.2-2.2a1 1 0 0 1 1-.25 11.4 11.4 0 0 0 3.6.57 1 1 0 0 1 1 1V20a1 1 0 0 1-1 1A17 17 0 0 1 3 4a1 1 0 0 1 1-1h3.5a1 1 0 0 1 1 1c0 1.25.2 2.45.57 3.57a1 1 0 0 1-.25 1z" fill="#000"/></svg></span>
    <div>Contact Us:<br><b>555 014 2290</b></div>
  </div>
  <div class="abs lang"><span class="flag"></span><div>Language<br>English ▾</div></div>
  <div class="abs search">
    <svg width="14" height="14" viewBox="0 0 24 24"><circle cx="10" cy="10" r="7" fill="none" stroke="#555" stroke-width="3"/><path d="M15 15l6 6" stroke="#555" stroke-width="3"/></svg>
    <span>Search</span>
    <span class="search-btn"><svg width="12" height="12" viewBox="0 0 24 24"><circle cx="10" cy="10" r="7" fill="none" stroke="#000" stroke-width="3"/><path d="M15 15l6 6" stroke="#000" stroke-width="3"/></svg></span>
  </div>
  <nav class="abs main-nav">
    <a style="left:0">HOME</a>
    <a style="left:97px">PRESENTATION</a>
    <a style="left:267px">OUR SERVICES</a>
    <a style="left:437px">OUR GALLERY</a>
    <a style="left:598px">CONTACT US</a>
  </nav>
</header>

<section class="hero">
  <div class="abs hero-photo" role="img" aria-label="Cemetery at dusk with a mourner holding red roses"></div>
  <div class="abs hero-figure" role="img" aria-label="Mourner in a dark coat holding a bouquet of red roses"></div>
  <div class="abs hero-brand">VIGIL LEDGER<br>SUITE</div>
  <p class="abs hero-copy">Sed ut perspiciatis unde omnis iste natus error sit voluptatem accusantium doloremque laudantium explicabo.</p>
  <svg class="swoosh" style="top:540px" height="100" viewBox="0 0 1200 100" preserveAspectRatio="none">
    <path d="M0 78 C300 40 700 60 1200 10 L1200 100 L0 100Z" fill="#000"/>
    <path d="M0 60 C300 30 700 50 1200 0 L1200 10 C700 60 300 44 0 82Z" fill="var(--yellow)"/>
  </svg>
</section>

<section class="about">
  <div class="abs about-photo" role="img" aria-label="Three colleagues reviewing a tablet together"></div>
  <div class="abs about-body">
    <h2 class="section-title">ABOUT US</h2>
    <p>Sed ut perspiciatis unde omnis iste natus error sit voluptatem accusantium doloremque laudantium, totam rem aperiam, eaque ipsa quae ab illo inventore veritatis et quasi architecto beatae vitae dicta sunt explicabo. Nemo enim ipsam voluptatem quia voluptas sit aspernatur aut odit aut fugit, sed quia consequuntur magni dolores eos qui ratione voluptatem sequi nesciunt.</p>
    <span class="btn">Read More</span>
  </div>
</section>

<section class="services" role="img" aria-label="Dark blue abstract technology background">
  <svg class="swoosh" style="top:0" height="70" viewBox="0 0 1200 70" preserveAspectRatio="none">
    <path d="M0 0 L1200 0 L1200 0 C800 20 400 40 0 50Z" fill="#000"/>
    <path d="M520 40 C800 30 1000 12 1200 0 L1200 12 C1000 22 800 38 520 40Z" fill="var(--yellow)"/>
  </svg>
  <h2 class="abs center section-title">OUR SERVICES</h2>
  <p class="abs lead" style="text-align:center">At vero eos et accusamus et iusto odio dignissimos ducimus qui blanditiis praesentium voluptatum deleniti atque corrupti quos dolores et quas molestias excepturi sint</p>

  <svg class="abs slide-arrow" style="left:44px" width="32" height="24" viewBox="0 0 32 24"><path d="M30 12H4M12 3 3 12l9 9" fill="none" stroke="#fff" stroke-width="2.5"/></svg>
  <svg class="abs slide-arrow" style="left:1126px" width="32" height="24" viewBox="0 0 32 24"><path d="M2 12h26M20 3l9 9-9 9" fill="none" stroke="#fff" stroke-width="2.5"/></svg>

  <article class="abs service-card" style="left:91px">
    <svg width="48" height="34" viewBox="0 0 48 34" style="margin:0 auto"><path d="M12 32a10 10 0 0 1-1-20 14 14 0 0 1 26 2 9 9 0 0 1-1 18z" fill="#fff"/></svg>
    <h3>ONLINE SOFTWARE</h3>
    <p>Sed ut perspiciatis unde omnis iste natus error sit voluptatem accusantium doloremque laudantium</p>
    <span class="read-more">Read More <svg width="14" height="10" viewBox="0 0 14 10"><path d="M0 5h11M8 1l4 4-4 4" fill="none" stroke="#fff" stroke-width="2"/></svg></span>
  </article>
  <article class="abs service-card" style="left:440px">
    <svg width="52" height="34" viewBox="0 0 52 34" style="margin:0 auto"><path d="M26 2 50 12 26 22 2 12z" fill="#fff"/><path d="M12 17v9c6 6 22 6 28 0v-9l-14 6z" fill="#fff"/><path d="M46 14v12" stroke="#fff" stroke-width="2"/></svg>
    <h3>SOFTWARE CUSTOMIZATION</h3>
    <p>Sed ut perspiciatis unde omnis iste natus error sit voluptatem accusantium doloremque laudantium</p>
    <span class="read-more">Read More <svg width="14" height="10" viewBox="0 0 14 10"><path d="M0 5h11M8 1l4 4-4 4" fill="none" stroke="#fff" stroke-width="2"/></svg></span>
  </article>
  <article class="abs service-card" style="left:789px">
    <svg width="34" height="40" viewBox="0 0 34 40" style="margin:0 auto"><rect x="2" y="5" width="30" height="33" rx="2" fill="#fff"/><rect x="11" y="1" width="12" height="7" rx="1" fill="#fff" stroke="#0b1420" stroke-width="2"/><path d="M8 16h4M15 16h12M8 23h4M15 23h12M8 30h4M15 30h12" stroke="#0b1420" stroke-width="2.5"/></svg>
    <h3>BILLING</h3>
    <p>Sed ut perspiciatis unde omnis iste natus error sit voluptatem accusantium doloremque laudantium</p>
    <span class="read-more">Read More <svg width="14" height="10" viewBox="0 0 14 10"><path d="M0 5h11M8 1l4 4-4 4" fill="none" stroke="#fff" stroke-width="2"/></svg></span>
  </article>

  <svg class="swoosh" style="top:624px" height="80" viewBox="0 0 1200 80" preserveAspectRatio="none">
    <path d="M0 40 C400 60 800 40 1200 0 L1200 80 L0 80Z" fill="#000"/>
    <path d="M0 22 C400 44 800 30 1200 0 L1200 0 C800 38 400 58 0 40Z" fill="var(--yellow)"/>
  </svg>
</section>

<section class="blog">
  <h2 class="abs center section-title">OUR BLOG</h2>
  <article class="abs post" style="left:91px">
    <div class="post-img" role="img" aria-label="Hands typing on a laptop keyboard"></div>
    <span class="post-date"><svg width="12" height="12" viewBox="0 0 12 12"><rect x="1" y="2" width="10" height="9" fill="none" stroke="#000" stroke-width="1.5"/><path d="M1 5h10" stroke="#000" stroke-width="1.5"/></svg>Oct 27 2018</span>
    <h3>SED UT PERSPICIATIS UND</h3>
    <p>Sed ut perspiciatis unde omnis iste natus error sit voluptatem accusantium doloremque laudantium, totam rem aperiam, eaque ipsa quae ab illo</p>
    <div class="more">READ MORE</div>
  </article>
  <article class="abs post" style="left:434px">
    <div class="post-img" role="img" aria-label="Illuminated corridor of server racks"></div>
    <span class="post-date"><svg width="12" height="12" viewBox="0 0 12 12"><rect x="1" y="2" width="10" height="9" fill="none" stroke="#000" stroke-width="1.5"/><path d="M1 5h10" stroke="#000" stroke-width="1.5"/></svg>Oct 27 2018</span>
    <h3>SED UT PERSPICIATIS UND</h3>
    <p>Sed ut perspiciatis unde omnis iste natus error sit voluptatem accusantium doloremque laudantium, totam rem aperiam, eaque ipsa quae ab illo</p>
    <div class="more">READ MORE</div>
  </article>
  <article class="abs post" style="left:783px">
    <div class="post-img" role="img" aria-label="Technicians working in a data center"></div>
    <span class="post-date"><svg width="12" height="12" viewBox="0 0 12 12"><rect x="1" y="2" width="10" height="9" fill="none" stroke="#000" stroke-width="1.5"/><path d="M1 5h10" stroke="#000" stroke-width="1.5"/></svg>Oct 27 2018</span>
    <h3>SED UT PERSPICIATIS UND</h3>
    <p>Sed ut perspiciatis unde omnis iste natus error sit voluptatem accusantium doloremque laudantium, totam rem aperiam, eaque ipsa quae ab illo</p>
    <div class="more">READ MORE</div>
  </article>
</section>

<section class="testimonials" role="img" aria-label="Dim server room background">
  <svg class="swoosh" style="top:0" height="60" viewBox="0 0 1200 60" preserveAspectRatio="none">
    <path d="M0 0 L1200 0 L1200 10 C900 20 700 40 500 50 L0 50Z" fill="#000"/>
    <path d="M600 46 C800 36 1000 20 1200 10 L1200 22 C1000 28 800 40 600 46Z" fill="var(--yellow)"/>
  </svg>
  <h2 class="abs center section-title">TESTIMONIALS</h2>
  <svg class="abs quote-mark" width="60" height="44" viewBox="0 0 60 44"><path d="M4 44V26C4 12 12 4 24 2v8c-6 2-9 6-9 12h9v22zM36 44V26c0-14 8-22 20-24v8c-6 2-9 6-9 12h9v22z" fill="#d8d8d8"/></svg>
  <blockquote class="abs">Sed ut perspiciatis unde omnis iste natus error sit voluptatem accusantium doloremque laudantium, totam rem aperiam, eaque ipsa quae ab illo inventore veritatis et quasi architecto beatae vitae dicta sunt explicabo.</blockquote>
  <div class="abs center author">Clara Wendt</div>
  <svg class="abs t-arrow" style="left:66px" width="64" height="40" viewBox="0 0 64 40"><path d="M62 20H6M24 3 6 20l18 17" fill="none" stroke="#fff" stroke-width="4"/></svg>
  <svg class="abs t-arrow" style="left:1070px" width="64" height="40" viewBox="0 0 64 40"><path d="M2 20h56M40 3l18 17-18 17" fill="none" stroke="#fff" stroke-width="4"/></svg>
  <svg class="swoosh" style="top:600px" height="80" viewBox="0 0 1200 80" preserveAspectRatio="none">
    <path d="M0 50 C400 60 800 40 1200 0 L1200 80 L0 80Z" fill="#000"/>
    <path d="M0 36 C300 44 500 40 700 20 C500 46 300 56 0 60Z" fill="var(--yellow)"/>
  </svg>
</section>

<section class="contact">
  <h2 class="abs center section-title">GET IN TOUCH</h2>
  <p class="abs lead" style="text-align:center">At vero eos et accusamus et iusto odio dignissimos ducimus qui blanditiis praesentium voluptatum deleniti atque corrupti quos dolores et quas molestias excepturi sint occaecati cupiditate non provident</p>
  <div class="abs field" style="left:161px;top:226px;width:432px"><svg width="11" height="11" viewBox="0 0 12 12"><circle cx="6" cy="3.5" r="3" fill="#fff"/><path d="M0 12a6 5 0 0 1 12 0z" fill="#fff"/></svg>First Name</div>
  <div class="abs field" style="left:607px;top:226px;width:432px"><svg width="11" height="11" viewBox="0 0 12 12"><circle cx="6" cy="3.5" r="3" fill="#fff"/><path d="M0 12a6 5 0 0 1 12 0z" fill="#fff"/></svg>Last Name</div>
  <div class="abs field" style="left:161px;top:278px;width:432px"><svg width="11" height="11" viewBox="0 0 12 12"><rect x="1" y="1" width="10" height="11" fill="#fff"/></svg>Company</div>
  <div class="abs field message" style="left:607px;top:278px;width:432px;height:150px"><svg width="11" height="11" viewBox="0 0 12 12"><path d="M1 1h10v7H5l-3 3V8H1z" fill="#fff"/></svg>Message :</div>
  <div class="abs field" style="left:161px;top:331px;width:432px"><svg width="12" height="10" viewBox="0 0 12 10"><rect width="12" height="10" fill="#fff"/><path d="M0 0l6 5 6-5" fill="none" stroke="#000" stroke-width="1.2"/></svg>Email Address</div>
  <div class="abs field" style="left:161px;top:387px;width:432px"><svg width="11" height="11" viewBox="0 0 24 24"><path d="M6.6 10.8a15 15 0 0 0 6.6 6.6l2.2-2.2a1 1 0 0 1 1-.25 11.4 11.4 0 0 0 3.6.57 1 1 0 0 1 1 1V20a1 1 0 0 1-1 1A17 17 0 0 1 3 4a1 1 0 0 1 1-1h3.5a1 1 0 0 1 1 1c0 1.25.2 2.45.57 3.57a1 1 0 0 1-.25 1z" fill="#fff"/></svg>Phone Number</div>
  <span class="abs btn submit"><svg width="18" height="18" viewBox="0 0 24 24"><path d="M2 11 22 2l-6 20-4-8z" fill="#000"/></svg>SUBMIT</span>
</section>

<footer class="site-footer" role="img" aria-label="Dim server room background">
  <svg class="swoosh" style="top:0" height="80" viewBox="0 0 1200 80" preserveAspectRatio="none">
    <path d="M0 0 L1200 0 L1200 30 C800 10 500 50 0 20Z" fill="#000"/>
    <path d="M300 28 C600 30 900 10 1200 30 L1200 44 C900 20 600 38 300 28Z" fill="var(--yellow)"/>
  </svg>
  <div class="abs center footer-brand">VIGIL LEDGER SUITE</div>
  <div class="abs info" style="left:154px">
    <div class="info-icon"><svg width="34" height="44" viewBox="0 0 24 32"><path d="M12 1a11 11 0 0 0-11 11c0 8 11 19 11 19s11-11 11-19A11 11 0 0 0 12 1z" fill="none" stroke="#000" stroke-width="2"/><circle cx="12" cy="12" r="4" fill="none" stroke="#000" stroke-width="2"/></svg></div>
    212 Alder Lane, Brookmere<br>Ohio - 40218
  </div>
  <div class="abs info" style="left:441px">
    <div class="info-icon"><svg width="40" height="40" viewBox="0 0 24 24"><path d="M6.6 10.8a15 15 0 0 0 6.6 6.6l2.2-2.2a1 1 0 0 1 1-.25 11.4 11.4 0 0 0 3.6.57 1 1 0 0 1 1 1V20a1 1 0 0 1-1 1A17 17 0 0 1 3 4a1 1 0 0 1 1-1h3.5a1 1 0 0 1 1 1c0 1.25.2 2.45.57 3.57a1 1 0 0 1-.25 1z" fill="none" stroke="#000" stroke-width="1.4"/></svg></div>
    Phone:<br>555 014 2290
  </div>
  <div class="abs info" style="left:720px">
    <div class="info-icon"><svg width="44" height="32" viewBox="0 0 44 32"><rect x="2" y="2" width="40" height="28" fill="none" stroke="#000" stroke-width="2.2"/><path d="M2 2l20 16L42 2M2 30l15-14M42 30 27 16" fill="none" stroke="#000" stroke-width="2.2"/></svg></div>
    Email:<br>hello@vigilledger.example
  </div>
  <div class="abs center footer-links">Home<span class="sep">|</span>Presentation<span class="sep">|</span>Our Services<span class="sep">|</span>Our Gallery<span class="sep">|</span>Contact Us</div>
  <div class="abs center copyright">© 2019 Vigil Ledger Suite. All right reserved</div>
  <div class="abs social"><span></span><span></span><span></span><span></span></div>
</footer>

</body>
</html>
```